Food Safety 1-California workers only

3.25" by 4.5" Black and White Magazine Ad
This ad is to train California workers only.
Workers will be trained on: Food Safety, FSMA (Food Safety Modernization Act), using equipment safety, food processing production skills, worker safety, supervisory skills, communication skills.
"FREE TRAINING", The company does the training or Harrowgate Instruction will provide the training.
Training grants range from $100,000 to $400,000.
Companies must be in business for profit.
Companies must train 200 employees or more.
This program is for California workers only.
Incumbent or new-hires are eligible.

Target Market(s)

California food processors, farms, food packaging, food processors, companies under FSMA, food safety, food production who need to train employees.

Industry/Entity Type

Food Production

Font styles to use
Serif
Sans Serif

Colors

Designer to choose colors to be used in the design.

Requirements
Must have
• This is a 3.25 inch by 4.5 inch magazine ad. It must be black and white. No color.
• The deliverable must be in basic PhotoShop. The ad does not need to include any graphics and be text only if needed. If you have a black and white graphic that will show well.
• Look at www.HGIPlateWatch..example
• Use the text from "TRAVO7-Photoshop-052018" file as your starting point.
Nice to have
• A black and white graphic about food. See www.HGIPlateWatch.example
Should not have
• No color.

```html
<!DOCTYPE html>
<html lang="en">
<head>
<meta charset="utf-8">
<title>Free Training Ad</title>
<link rel="stylesheet" href="https://fonts.googleapis.com/css2?family=Fira+Sans+Extra+Condensed:wght@300;400;600;700&family=Source+Sans+3:wght@300;400;600;700&display=swap">
<style>
  :root {
    --ink: #111111;
    --paper: #ffffff;
    --backdrop: #e8f0f8;
  }
  * { margin: 0; padding: 0; box-sizing: border-box; }
  html, body { width: 1200px; height: 1200px; overflow: hidden; background: var(--backdrop); }
  .ad {
    position: absolute; left: 191px; top: 33px;
    width: 818px; height: 1134px;
    background: var(--paper); color: var(--ink);
    font-family: "Source Sans 3", sans-serif;
  }
  .ad > * { position: absolute; }
  .header-band { left: 32px; top: 32px; width: 755px; height: 218px; }
  .footer-band { left: 32px; top: 1001px; width: 755px; height: 102px; }
  .headline {
    left: 0; width: 100%; top: 38px; text-align: center;
    font-family: "Fira Sans Extra Condensed", sans-serif; font-weight: 700;
    font-size: 132px; line-height: 132px; color: var(--paper); letter-spacing: -1px;
    white-space: nowrap;
  }
  .topics {
    left: 32px; width: 755px; top: 160px; text-align: center;
    font-family: "Fira Sans Extra Condensed", sans-serif; font-weight: 400;
    font-size: 30px; line-height: 32px; color: var(--paper); letter-spacing: -0.4px;
    white-space: nowrap;
  }
  .quote {
    left: 0; width: 100%; text-align: center;
    font-weight: 300; font-size: 40px; line-height: 39px; letter-spacing: -0.5px;
    white-space: nowrap;
  }
  .quote b { font-weight: 700; }
  .quote-one { top: 254px; }
  .quote-two { top: 379px; }
  .divider { left: 247px; top: 337px; width: 324px; height: 30px; display: flex; align-items: center; gap: 12px; }
  .divider::before, .divider::after { content: ""; flex: 1; height: 2px; background: var(--ink); }
  .divider span { font-weight: 700; font-size: 28px; line-height: 28px; }
  .qualify-box {
    left: 32px; top: 493px; width: 755px; height: 293px;
    border: 2px solid var(--ink); border-radius: 12px;
  }
  .qualify-title {
    left: 0; width: 100%; top: 476px; text-align: center;
  }
  .qualify-title span {
    background: var(--paper); padding: 0 20px;
    font-weight: 400; font-size: 31px; line-height: 36px; letter-spacing: -0.5px;
  }
  .requirements {
    left: 100px; top: 522px; list-style: none;
    font-weight: 300; font-size: 28px; line-height: 37px; letter-spacing: -0.3px;
  }
  .requirements li { position: relative; padding-left: 26px; white-space: nowrap; }
  .requirements li::before {
    content: ""; position: absolute; left: 0; top: 16px;
    width: 7px; height: 7px; border-radius: 50%; background: var(--ink);
  }
  .condensed { font-family: "Fira Sans Extra Condensed", sans-serif; }
  .contact-label {
    left: 118px; top: 812px; width: 178px; height: 62px;
    border-top: 2px solid var(--ink); border-bottom: 2px solid var(--ink);
    font-weight: 300; font-size: 54px; line-height: 58px;
  }
  .contact-name { left: 338px; top: 808px; font-weight: 600; font-size: 33px; line-height: 36px; white-space: nowrap; }
  .contact-company { left: 338px; top: 850px; font-weight: 600; font-size: 28px; line-height: 32px; letter-spacing: -0.3px; white-space: nowrap; }
  .contact-lines { font-size: 26px; line-height: 37px; font-weight: 400; white-space: nowrap; }
  .address { left: 118px; top: 890px; }
  .web { left: 400px; top: 890px; }
  .phone {
    left: 0; width: 100%; top: 1054px; text-align: center;
    font-weight: 700; font-size: 35px; line-height: 40px; color: var(--paper); letter-spacing: 0.5px;
  }
</style>
</head>
<body>
<div class="ad">
  <svg class="header-band" viewBox="0 0 755 218" aria-hidden="true">
    <path d="M0 14 Q0 0 14 0 H741 Q755 0 755 14 V176 Q380 150 0 196 Z" fill="var(--ink)"/>
    <path d="M0 218 V206 Q380 160 755 188 V200 Q380 176 0 218 Z" fill="var(--ink)"/>
  </svg>
  <div class="headline">FREE TRAINING</div>
  <div class="topics">FOOD SAFETY • FSMA • PRODUCTION SKILLS • WORKER SAFETY</div>

  <p class="quote quote-one">“<b>YOU DO</b> THE TRAINING AND<br>THE STATE OF <b>CALIFORNIA PAYS FOR IT!</b>”</p>
  <div class="divider"><span>OR</span></div>
  <p class="quote quote-two">“<b>WE DO</b> THE TRAINING AND<br><b>THE STATE PAYS FOR IT!</b>”</p>

  <div class="qualify-box"></div>
  <div class="qualify-title"><span>HOW TO QUALIFY:</span></div>
  <ul class="requirements">
    <li>Train California Workers Only</li>
    <li>Trainees must earn $11/hour</li>
    <li>Full-time workers only</li>
    <li>Employees must attend at least 8 Hours of training</li>
    <li>You must train 200 or more employees</li>
    <li>Incumbent or New-Hire workers are eligible</li>
    <li>Seasonal workers are eligible</li>
  </ul>

  <div class="contact-label condensed">CONTACT:</div>
  <div class="contact-name">Warren Castell</div>
  <div class="contact-company condensed">Harrowgate Instruction Company, Inc.</div>
  <div class="contact-lines address condensed">1200 Lindqvist Parkway<br>Suite 250<br>Marlow Vale, CA 90000</div>
  <div class="contact-lines web condensed">www.HGICAL.example<br>www.HGIPlateWatch.example<br>email: W.Castell@HGICAL.example</div>

  <svg class="footer-band" viewBox="0 0 755 102" aria-hidden="true">
    <path d="M0 0 Q380 30 755 8 V14 Q380 44 0 14 Z" fill="var(--ink)"/>
    <path d="M0 26 Q380 48 755 20 V88 Q755 102 741 102 H14 Q0 102 0 88 Z" fill="var(--ink)"/>
  </svg>
  <div class="phone">Phone. (555) 014-3200</div>
</div>
</body>
</html>
```